High-end construction company needs a business card design

We need a modern looking business card that draws people in, is memorable and looks so good people will want to sick it on their fridges.
On the first side what is needed are:
Logo
My name - Tomasz Brelwik
Title - Managing Director
Website - www.varkelt.co.uk
Email - tomasz@varkelt.co.uk
Telephone - 020 5194 6281
Mobile - 07845139072
On the back side was is needed is a list of all the services we provide:
-Kitchen Renovations
-Bathroom Renovations
-House Renovations
-Garage Conversions
-Extensions
-Loft Conversions
-Conservatories
-Carpentry
-Tiling
-Electrical
-Plumbing & Heating
-Bricklaying
-Landscaping
-Decorating
-Plastering
We would like the colours to be the same shades as on the logo with grey or black for the words.
Target Market(s)
Anyone who needs building work done
Contact Information for Business Card
This business card is for a construction company which strives to deliver excellent service and quality.
The look and feel of the card should represent this.
Requirements
Must have
- On the first side what is needed are:
Logo
My name - Tomasz Brelwik
Title - Managing Director
Website - www.varkelt.co.uk
Email - tomasz@varkelt.co.uk
Telephone - 020 5194 6281
Mobile - 07845139072
Nice to have
- Cool looking features

```html
<!DOCTYPE html>
<html lang="en">
<head>
<meta charset="utf-8">
<title>Varkelt Construction Ltd – Business Card</title>
<link href="https://fonts.googleapis.com/css2?family=Montserrat:wght@600;700;800&family=Open+Sans:wght@400;600&display=swap" rel="stylesheet">
<style>
  :root {
    --bg: #262626;
    --green: #3f8a36;
    --green-dark: #347a2d;
    --green-light: #6cbf3d;
    --white: #ffffff;
    --grey: #6b6b6b;
  }
  * { margin: 0; padding: 0; box-sizing: border-box; }
  html, body { width: 1200px; height: 900px; overflow: hidden; }
  body {
    background: var(--bg);
    font-family: "Open Sans", sans-serif;
    position: relative;
  }
  .card {
    position: absolute;
    left: 300px;
    width: 600px;
    height: 343px;
    overflow: hidden;
    box-shadow: 0 10px 30px rgba(0,0,0,.45);
  }
  .card-front { top: 90px; background: var(--white); }
  .card-back {
    top: 493px;
    background: linear-gradient(160deg, var(--green-dark), var(--green) 60%, #4a9640);
    color: var(--white);
    text-align: center;
  }
  .front-waves { position: absolute; inset: 0; }
  .wordmark {
    font-family: "Montserrat", sans-serif;
    font-weight: 800;
    line-height: 1;
  }
  .card-front .wordmark {
    position: absolute; left: 38px; top: 36px; color: var(--green);
  }
  .wordmark-name { display: block; font-size: 46px; letter-spacing: 1px; }
  .wordmark-sub { display: block; font-size: 13px; letter-spacing: 3.2px; margin-top: 6px; }
  .person {
    position: absolute; left: 372px; top: 148px;
  }
  .person-name {
    font-family: "Montserrat", sans-serif;
    font-weight: 800; font-size: 23px; color: var(--green);
    letter-spacing: .5px;
  }
  .person-title { font-size: 17px; color: var(--grey); margin-top: 2px; }
  .contacts {
    position: absolute; right: 250px; bottom: 28px;
    list-style: none; color: var(--white); text-align: right;
    font-size: 16px; line-height: 22px;
  }
  .contacts li { display: flex; justify-content: flex-end; align-items: center; gap: 8px; }
  .contact-icon { width: 14px; height: 14px; flex: none; }
  .card-back .wordmark { color: var(--white); margin-top: 46px; }
  .card-back .wordmark-name { font-size: 50px; }
  .card-back .wordmark-sub { font-size: 14px; letter-spacing: 3.6px; }
  .services-heading {
    display: flex; align-items: center; justify-content: center; gap: 12px;
    margin: 18px auto 10px; width: 460px;
    font-family: "Montserrat", sans-serif; font-weight: 600;
    font-size: 16px; letter-spacing: 1px; color: var(--green-light);
  }
  .services-heading::before, .services-heading::after {
    content: ""; flex: 1; height: 1px; background: var(--green-light);
  }
  .services-list { list-style: none; font-size: 14.5px; line-height: 22px; }
  .services-list .bullet { color: var(--green-light); margin: 0 3px; }
</style>
</head>
<body>

<section class="card card-front" aria-label="Business card front">
  <svg class="front-waves" viewBox="0 0 600 343" width="600" height="343" aria-hidden="true">
    <path d="M0,135 C220,150 450,245 578,343 L0,343 Z" fill="#6cbf3d"/>
    <path d="M0,146 C215,162 440,252 550,343 L0,343 Z" fill="#ffffff"/>
    <path d="M0,152 C210,172 425,260 528,343 L0,343 Z" fill="#3f8a36"/>
  </svg>

  <div class="wordmark">
    <span class="wordmark-name">VARKELT</span>
    <span class="wordmark-sub">CONSTRUCTION LTD</span>
  </div>

  <div class="person">
    <div class="person-name">TOMASZ BRELWIK</div>
    <div class="person-title">Managing Director</div>
  </div>

  <ul class="contacts">
    <li>020 5194 6281
      <svg class="contact-icon" viewBox="0 0 16 16"><path d="M3 1l3 3-1.5 2a9 9 0 0 0 5.5 5.5L12 10l3 3-2 2C7 15 1 9 1 3z" fill="#6cbf3d"/></svg>
    </li>
    <li>07845139072
      <svg class="contact-icon" viewBox="0 0 16 16"><rect x="4" y="1" width="8" height="14" rx="1.5" fill="none" stroke="#6cbf3d" stroke-width="1.6"/><circle cx="8" cy="12.5" r="1" fill="#6cbf3d"/></svg>
    </li>
    <li>tomasz@varkelt.co.uk
      <svg class="contact-icon" viewBox="0 0 16 16"><rect x="1" y="3" width="14" height="10" fill="#6cbf3d"/><path d="M1 3l7 6 7-6" fill="none" stroke="#3f8a36" stroke-width="1.3"/></svg>
    </li>
    <li>www.varkelt.co.uk
      <svg class="contact-icon" viewBox="0 0 16 16"><circle cx="8" cy="8" r="7" fill="#6cbf3d"/><path d="M1 8h14M8 1c-3 3-3 11 0 14M8 1c3 3 3 11 0 14" fill="none" stroke="#3f8a36" stroke-width="1"/></svg>
    </li>
  </ul>
</section>

<section class="card card-back" aria-label="Business card back">
  <div class="wordmark">
    <span class="wordmark-name">VARKELT</span>
    <span class="wordmark-sub">CONSTRUCTION LTD</span>
  </div>
  <h2 class="services-heading">SERVICES</h2>
  <ul class="services-list">
    <li><span class="bullet">•</span>Kitchen Renovations <span class="bullet">•</span>Bathroom Renovations <span class="bullet">•</span>House Renovations</li>
    <li><span class="bullet">•</span>Garage Conversions <span class="bullet">•</span>Extensions <span class="bullet">•</span>Loft Conversions <span class="bullet">•</span>Conservatories</li>
    <li><span class="bullet">•</span>Carpentry <span class="bullet">•</span>Tiling <span class="bullet">•</span>Electrical <span class="bullet">•</span>Plumbing &amp; Heating</li>
    <li><span class="bullet">•</span>Bricklaying <span class="bullet">•</span>Landscaping <span class="bullet">•</span>Decorating <span class="bullet">•</span>Plastering</li>
  </ul>
</section>

</body>
</html>
```